Small Business Broker Business Card Design

A business card design for a small business brokerage, which is a financial service, not unlike real estate brokerage, but for small businesses such as laundromats, pizza shops, restaurants, cleaners etc. The designs should all be simple, more conservative in nature, using the colors and font of the logo. Again, think real estate Brokerage as a business context
Contact Information for Business Card
Name: Glen R. Harlow. Title: Small Business Advisor. Email: g.harlow@bayfieldcapitalworks.example. Mobile: (555) 274-3918. Office: (555) 806-2147. www.bayfieldcapitalworks.example

```html
<!DOCTYPE html>
<html lang="en">
<head>
<meta charset="utf-8">
<title>Bayfield Capital Works – Business Card</title>
<link rel="stylesheet" href="https://fonts.googleapis.com/css2?family=Montserrat:wght@400;500;600;700;800&display=swap">
<style>
  :root {
    --navy: #1b3a6f;
    --navy-deep: #132c58;
    --green: #86c440;
    --ink: #222a36;
    --white: #ffffff;
    --stage: #e9ebef;
  }
  * { box-sizing: border-box; margin: 0; padding: 0; }
  html, body { width: 1200px; height: 800px; overflow: hidden; }
  body {
    background: var(--stage);
    font-family: "Montserrat", sans-serif;
    display: flex;
    align-items: center;
    justify-content: center;
    gap: 40px;
  }
  .card {
    position: relative;
    width: 560px;
    height: 320px;
    border-radius: 18px;
    overflow: hidden;
    box-shadow: 0 6px 18px rgba(0,0,0,0.18);
  }

  /* Back */
  .card-back { background: var(--navy); }
  .card-back .texture {
    position: absolute; inset: 0;
    background: linear-gradient(160deg, #2a4d8a 0%, var(--navy) 40%, var(--navy-deep) 100%);
  }
  .card-back .brand {
    position: absolute; left: 0; right: 0; top: 50%;
    transform: translateY(-50%);
    text-align: center;
  }
  .card-back .brand-name {
    color: var(--white);
    font-weight: 700;
    font-size: 22px;
    letter-spacing: 0.5px;
    text-transform: uppercase;
  }
  .card-back .brand-tagline {
    color: var(--green);
    font-weight: 600;
    font-size: 10.5px;
    letter-spacing: 1.4px;
    text-transform: uppercase;
    margin-top: 6px;
  }

  /* Front */
  .card-front { background: var(--white); }
  .card-front .brand {
    position: absolute; left: 30px; top: 128px; width: 236px;
  }
  .card-front .brand-name {
    color: var(--navy);
    font-weight: 700;
    font-size: 16px;
    line-height: 1.15;
    text-transform: uppercase;
  }
  .card-front .brand-tagline {
    color: var(--green);
    font-weight: 600;
    font-size: 7.6px;
    letter-spacing: 0.9px;
    text-transform: uppercase;
    margin-top: 5px;
  }
  .divider {
    position: absolute; left: 276px; top: 78px;
    width: 1.5px; height: 150px;
    background: var(--navy);
  }
  .contact {
    position: absolute; left: 292px; top: 74px; width: 260px;
  }
  .person-name {
    font-weight: 800;
    font-size: 23px;
    color: var(--navy);
    line-height: 1.1;
  }
  .person-name .surname { color: var(--green); }
  .person-title {
    font-size: 11.5px;
    color: var(--ink);
    margin-top: 2px;
  }
  .contact-list { list-style: none; margin-top: 16px; }
  .contact-list li {
    display: flex; align-items: center; gap: 7px;
    font-size: 10px;
    color: var(--ink);
    line-height: 1;
    margin-bottom: 9px;
    white-space: nowrap;
  }
  .contact-list svg { width: 11px; height: 11px; flex: none; fill: var(--navy); }
  .edge-bands { position: absolute; left: 0; bottom: 0; width: 560px; height: 40px; }
</style>
</head>
<body>

  <section class="card card-back" aria-label="Card back">
    <div class="texture" role="img" aria-label="Navy background with a faint repeating brand pattern"></div>
    <div class="brand">
      <div class="brand-name">Bayfield Capital Works, Inc</div>
      <div class="brand-tagline">Confidently buy or sell a local business today</div>
    </div>
  </section>

  <section class="card card-front" aria-label="Card front">
    <div class="brand">
      <div class="brand-name">Bayfield Capital Works, Inc</div>
      <div class="brand-tagline">Confidently buy or sell a local business today</div>
    </div>

    <div class="divider"></div>

    <div class="contact">
      <h1 class="person-name">Glen R. <span class="surname">Harlow</span></h1>
      <p class="person-title">Small Business Advisor</p>
      <ul class="contact-list">
        <li>
          <svg viewBox="0 0 24 24" aria-hidden="true"><path d="M3 8c0-2 4-4 9-4s9 2 9 4v2h-5V8H8v2H3z"/><rect x="5" y="12" width="14" height="9" rx="2"/></svg>
          (555) 806-2147
        </li>
        <li>
          <svg viewBox="0 0 24 24" aria-hidden="true"><path d="M6.6 10.8a15 15 0 0 0 6.6 6.6l2.2-2.2a1 1 0 0 1 1-.25 11.4 11.4 0 0 0 3.6.57 1 1 0 0 1 1 1V20a1 1 0 0 1-1 1A17 17 0 0 1 3 4a1 1 0 0 1 1-1h3.5a1 1 0 0 1 1 1c0 1.25.2 2.45.57 3.6a1 1 0 0 1-.25 1z"/></svg>
          (555) 274-3918
        </li>
        <li>
          <svg viewBox="0 0 24 24" aria-hidden="true"><path d="M2 5h20v14H2z M2 5l10 8 10-8" fill="var(--navy)"/><path d="M3 6l9 7 9-7" fill="none" stroke="#fff" stroke-width="1.5"/></svg>
          g.harlow@bayfieldcapitalworks.example
        </li>
        <li>
          <svg viewBox="0 0 24 24" aria-hidden="true"><circle cx="12" cy="12" r="10"/><path d="M2 12h20M12 2c3 3 3 17 0 20M12 2c-3 3-3 17 0 20" fill="none" stroke="#fff" stroke-width="1.3"/></svg>
          www.bayfieldcapitalworks.example
        </li>
      </ul>
    </div>

    <svg class="edge-bands" viewBox="0 0 560 40" aria-hidden="true">
      <polygon points="0,32 345,32 337,40 0,40" fill="var(--navy)"/>
      <polygon points="352,32 360,18 560,18 560,40 344,40" fill="var(--green)"/>
    </svg>
  </section>

</body>
</html>
```